Brookvane Consulting Business Card Design

Business Card Design for Brookvane Consulting. Brookvane Consulting is a boutique consultancy based in Atlanta, GA., that specializes in marketing strategy, organization planning, and leadership development. We provide solutions for small businesses and startups as well as Vantage 300 companies.

http://brookvaneconsulting.com/

Target Market(s)

We provide solutions for small businesses and startups as well as Vantage 300 companies.

Industry/Entity Type

Consulting

Contact Information for Business Card

Two sided business card with priority on contact information, logo, tag line (Guidance to Plan Wisely, Lead Boldly, Grow Further)

Colors

Designer to choose colors to be used in the design.

Requirements
Must have
• contact information, logo, tag line (Guidance to Plan Wisely, Lead Boldly, Grow Further)
• Simple no over communication.
Nice to have
• I would like to see different placements of logo and creative use of both sides of the card
Should not have
• Do not put too much information on the card.

```html
<!DOCTYPE html>
<html lang="en">
<head>
<meta charset="utf-8">
<title>Brookvane Consulting Business Card</title>
<link rel="stylesheet" href="https://fonts.googleapis.com/css2?family=Lato:wght@300;400;700&family=Kaushan+Script&display=swap">
<style>
  :root {
    --stage: #3a332f;
    --card-white: #ffffff;
    --card-black: #161616;
    --panel-grey: #b9b9b9;
    --ink: #111111;
    --paper-text: #f2f2f2;
  }
  * { margin: 0; padding: 0; box-sizing: border-box; }
  html, body {
    width: 1200px;
    height: 769px;
    overflow: hidden;
    background: var(--stage);
  }
  .canvas {
    position: relative;
    width: 1200px;
    height: 769px;
  }
  .card {
    position: absolute;
    top: 236px;
    width: 520px;
    height: 297px;
    overflow: hidden;
    box-shadow: 0 14px 30px rgba(0,0,0,0.45);
  }
  .card--front { left: 60px; background: var(--card-white); }
  .card--back  { left: 620px; background: var(--card-black); }

  .front-panel {
    position: absolute;
    inset: 0;
    width: 100%;
    height: 100%;
  }
  .contact {
    position: absolute;
    left: 34px;
    top: 128px;
    color: var(--ink);
    font-family: "Lato", sans-serif;
  }
  .contact__name {
    font-family: "Kaushan Script", cursive;
    font-size: 28px;
    font-weight: 400;
    line-height: 1;
  }
  .contact__title {
    font-size: 15px;
    margin-top: 6px;
  }
  .contact__rule {
    width: 30px;
    height: 2px;
    background: var(--ink);
    margin: 16px 0 14px;
  }
  .contact__line {
    font-size: 14px;
    line-height: 1.35;
  }

  .brand {
    position: absolute;
    left: 0;
    right: 0;
    top: 92px;
    text-align: center;
    color: var(--paper-text);
    font-family: "Lato", sans-serif;
  }
  .brand__name {
    display: inline-flex;
    align-items: center;
    gap: 12px;
    font-size: 38px;
    font-weight: 400;
    letter-spacing: 1px;
  }
  .brand__dot {
    width: 12px;
    height: 12px;
    border-radius: 50%;
    background: var(--paper-text);
  }
  .brand__tagline {
    margin-top: 40px;
    font-size: 13px;
    font-weight: 400;
    letter-spacing: 0.3px;
  }
</style>
</head>
<body>
<main class="canvas">
  <section class="card card--front" aria-label="Business card front">
    <svg class="front-panel" viewBox="0 0 520 297" preserveAspectRatio="none" aria-hidden="true">
      <polygon points="300,0 520,0 520,297 375,297" fill="var(--panel-grey)"/>
    </svg>
    <div class="contact">
      <p class="contact__name">Desmond Hale</p>
      <p class="contact__title">Founder/Managing Director</p>
      <div class="contact__rule"></div>
      <p class="contact__line">424-555-0142</p>
      <p class="contact__line">desmond@brookvaneconsulting.com</p>
      <p class="contact__line">brookvaneconsulting.com</p>
    </div>
  </section>

  <section class="card card--back" aria-label="Business card back">
    <div class="brand">
      <p class="brand__name"><span class="brand__dot"></span>Brookvane Consulting</p>
      <p class="brand__tagline">Guidance to Plan Wisely, Lead Boldly, Grow Further</p>
    </div>
  </section>
</main>
</body>
</html>
```